ECommerce Site Redesign: overall site and specific pages

We have a website that has been in operation for 6+ years, and it's time for a visual refresh.

Our current website is located at http://qlt.example

The only significant functional change will be the movement of the persistent vertical navigation bar from the left side up to a categorized horizontal navigation menu. I've attached a rough mockup of how we want this positioned.

No coding necessary; just PSDs. The attached ROUGH MENU MOCKUP.PSD contains a layer with our logo on white should you wish to include it in your submissions.

Target Market(s)

We are an outdoor retailer focused on the high end of the market. We have a general color scheme on our site which we'd like to keep, but various elements need to be made consistent and more aesthetically pleasing.

Our brand is very important to us, and the site design must reflect our values of high quality and affluence. We cater to outdoor enthusiasts, hikers, back packers, and general high end apparel consumers.

Requirements
Must have
• In order to address the issue of consistency, we require strict design guidelines, including font sizing, element spacing, etc.

We require 7 page design templates for:

1.) overall site template - see http://qlt.example for current.
* narrow static header bar (NEW)
* footer (KEEP SAME/SIMILAR)
* background
* body
* mini-cart (collapsed and expanded)
* promotion panel (ad box, rotating featured items)
* horizontal navigation bars (expanded/collapsed, grouped by 7 main categories) - see attached ROUGH MENU MOCKUP and see additional notes.
* recently viewed products

2.) product page (see http://qlt.example/270599/frostwing_summit-hood-pure-plus-mens.aspx for current)
* product imagery/zoombox
* color, size, quantity selection
* add to cart button
* detail tabs
* In-store Availability info
* info panel near the add to cart box for exceptions including:
- Available to pick up in-store only
- Free shipping for your entire order when you purchase this item
- This item is over-sized; please contact a store directly
* "customers who bought this also bought" panel, grid listing of items

3.) product listings (category, search results, etc.)
* item thumbnails in grid format
* sidebar for refinement options (by supplier, by price, by size, etc.)

4.) generic information/content page (see http://qlt.example/t-returns.aspx)

5.) store locations page (see http://qlt.example/t-QLT.stores.04.aspx)
* store details
* map
* hours
* contact info
* local links
* contact form

6.) contact us form

7.) checkout (see attached current checkout screen shot)
* cart summary
* checkout steps

Any visual elements benefiting from hover effects will need to have both dimmed and hovered layers in the design.

```html
<!DOCTYPE html>
<html lang="en">
<head>
<meta charset="utf-8">
<title>Quillton Peak Outfitters – Womens Jackets &amp; Coats</title>
<link href="https://fonts.googleapis.com/css2?family=Ubuntu:wght@400;500;700&family=Arimo:wght@400;700&display=swap" rel="stylesheet">
<style>
:root{
  --blue:#2a7ac3;
  --blue-text:#1b62a8;
  --purple:#9a7fc2;
  --purple-frame:#a58bcb;
  --purple-light:#b9a4d8;
  --panel:#f1eff6;
  --ink:#333333;
  --bar:#111111;
}
*{margin:0;padding:0;box-sizing:border-box}
html,body{width:1200px;height:869px;overflow:hidden}
body{position:relative;font-family:"Arimo",Arial,sans-serif;color:var(--ink);
  background:linear-gradient(180deg,#5d95cf 0,#b7cfe6 140px,#e9eef4 330px,#f5f7fa 656px)}
.abs{position:absolute}
a{color:inherit;text-decoration:none}

/* top utility bar */
.utility{left:551px;top:3px;width:474px;height:30px;background:var(--bar);display:flex;align-items:center;
  font-size:8.5px;letter-spacing:.5px;color:#ddd;text-transform:uppercase;padding-left:23px;white-space:nowrap}
.utility .sep{width:1px;height:12px;background:#555;margin:0 7px;flex:none}
.utility .search{margin-left:14px;width:93px;height:17px;background:#fff;display:flex;align-items:center;justify-content:space-between;
  color:#999;font-size:8px;padding-left:4px;flex:none}
.utility .search span.btn{width:17px;height:17px;background:#bbb;display:flex;align-items:center;justify-content:center}
.utility .cart{margin-left:18px;display:flex;align-items:center;gap:4px}
.utility .checkout{margin-left:18px}

/* header */
.masthead{left:0;top:33px;width:1200px;height:66px;background:linear-gradient(180deg,#fff 0,#f4f4f6 70%,#dfe2e8 100%)}
.brand{left:172px;top:40px;display:flex;align-items:center;gap:10px}
.brand .mark{width:22px;height:22px;border-radius:50%;background:var(--purple)}
.brand .name{font-family:"Ubuntu",sans-serif;font-weight:700;font-size:36px;color:#7b5aae;letter-spacing:.5px}
.brand-sub{left:204px;top:80px;font-family:"Ubuntu",sans-serif;font-weight:700;font-size:9px;letter-spacing:16px;color:#7b5aae}
.tollfree{left:690px;top:54px;display:flex;align-items:center;gap:8px;font-family:Georgia,"Times New Roman",serif}
.tollfree .label{font-size:19px;color:#2f6fb0}
.tollfree .num{font-size:23px;color:#333}

/* main navigation */
.mainnav{left:0;top:99px;width:1200px;height:49px;background:linear-gradient(180deg,#3388d3,#2673bd)}
.mainnav ul{list-style:none;position:absolute;left:186px;top:0;height:49px;display:flex}
.mainnav li{height:49px;display:flex;align-items:center;justify-content:center;font-family:"Ubuntu",sans-serif;
  font-weight:500;font-size:13.5px;color:#fff;border-right:1px solid rgba(0,0,0,.12)}
.mainnav li.active{background:#5a98d6}

/* content frame */
.frame{left:179px;top:148px;width:843px;height:491px;background:var(--purple-frame)}
.hero{left:186px;top:153px;width:828px;height:104px;border:1px solid #d8d8d8;
  background:linear-gradient(90deg,#5a4a33 0,#6b6a40 35%,#3e5a2e 60%,#33506a 85%,#2c4a66 100%)}
.sidebar{left:186px;top:260px;width:261px;height:365px;background:var(--purple)}
.sidebar ul{list-style:none}
.sidebar li{position:absolute;left:14px;font-family:"Ubuntu",sans-serif;font-weight:500;font-size:13px;color:#fff;text-transform:uppercase}
.sidebar .current{left:0;top:0;width:261px;height:32px;background:var(--panel)}
.sidebar li.on{color:var(--blue-text)}
.content{left:447px;top:260px;width:567px;height:365px;background:var(--panel)}

.cat-thumb{left:474px;top:289px;width:56px;height:56px;border:2px solid var(--purple-light);background:#fff;padding:4px}
.cat-thumb div{width:100%;height:100%;background:linear-gradient(180deg,#e8323a,#c4161f)}
.cat-title{left:543px;top:285px;font-family:"Ubuntu",sans-serif;font-weight:500;font-size:22px;color:var(--blue-text);letter-spacing:.3px}
.links{font-size:10.5px;color:#333;line-height:13.8px}
.intro{left:475px;top:404px;width:490px;font-size:10.5px;line-height:15.7px;color:#666}

.subcats{left:447px;top:459px;width:335px;height:166px;background:#fff}
.subcat{position:absolute;top:12px;width:76px}
.subcat h3{font-size:10.5px;font-weight:700;color:var(--blue-text);line-height:13.5px;height:28px}
.subcat .img{margin-top:4px;width:76px;height:76px;border:2px solid var(--purple-light);padding:4px}
.subcat .img div{width:100%;height:100%}

.featured-title{left:800px;top:467px;font-family:"Ubuntu",sans-serif;font-weight:500;font-size:14px;color:#333;letter-spacing:.3px}
.next{left:970px;top:469px;width:16px;height:16px;background:#777}
.product{position:absolute;top:509px;width:65px}
.product .img{width:65px;height:65px;border:2px solid var(--purple-light);background:#fff;padding:5px}
.product .img div{width:100%;height:100%;border-radius:8px}
.product p{margin-top:7px;font-size:10.5px;font-weight:700;color:var(--blue-text);white-space:nowrap}

/* footer */
.footer{left:0;top:656px;width:1200px;height:213px;background:var(--blue)}
.brands{left:179px;top:682px;width:514px;height:77px;border:1px solid #fff;padding:3px}
.brands .inner{width:100%;height:100%;background:#fff;display:flex;align-items:center;justify-content:space-around;padding:0 8px}
.brands span{font-weight:700;font-size:11px;color:#444;display:flex;align-items:center;gap:4px}
.brands i{display:inline-block;width:8px;height:8px;background:#777}
.footlinks{left:186px;top:786px;font-size:9.5px;color:#fff;display:flex;gap:10px;text-transform:uppercase;letter-spacing:.1px;white-space:nowrap}
.copyright{left:185px;top:808px;font-size:10.5px;font-weight:700;color:#fff}
.foot-h{font-size:10.5px;font-weight:700;color:#fff}
.stores{font-size:10.5px;color:#e8f0fa;line-height:15.5px;list-style:none;white-space:nowrap}
.social{left:884px;top:706px;display:flex;gap:9px}
.social span{width:31px;height:31px;border-radius:50%;background:#fff;display:block}
.contact-row{font-size:11px;color:#fff;display:flex;align-items:center;gap:10px;white-space:nowrap}
</style>
</head>
<body>

<div class="abs utility">
  <a href="#">Store Locator</a><span class="sep"></span><a href="#">Customer Service</a>
  <div class="search">Search<span class="btn"><svg width="9" height="9" viewBox="0 0 10 10"><circle cx="4" cy="4" r="3" fill="none" stroke="#333" stroke-width="1.3"/><line x1="6.2" y1="6.2" x2="9.5" y2="9.5" stroke="#333" stroke-width="1.4"/></svg></span></div>
  <div class="cart"><svg width="15" height="11" viewBox="0 0 15 11"><path d="M0 1h3l2 6h7l2-5H4" fill="none" stroke="#ccc" stroke-width="1.2"/><circle cx="6" cy="9.5" r="1.2" fill="#ccc"/><circle cx="11" cy="9.5" r="1.2" fill="#ccc"/></svg>0 Items</div>
  <a class="checkout" href="#">Checkout</a>
</div>

<header>
  <div class="abs masthead"></div>
  <div class="abs brand"><span class="mark"></span><span class="name">QUILLTON PEAK</span></div>
  <div class="abs brand-sub">OUTFITTERS</div>
  <div class="abs tollfree">
    <span class="label">TOLL FREE!</span>
    <svg width="16" height="17" viewBox="0 0 16 17"><path d="M3 1l3 0 1 4-2 1.5c1 2.5 2.5 4 5 5l1.5-2 4 1v3c0 1-1 2-2 2C6 15 1 10 1 3c0-1 1-2 2-2z" fill="#7b5aae"/></svg>
    <span class="num">1-866-555-PEAK</span>
  </div>
</header>

<nav class="abs mainnav">
  <ul>
  <li style="width:99px">HOME</li>
  <li class="active" style="width:101px">WOMEN</li>
  <li style="width:97px">MENS</li>
  <li style="width:80px">GEAR</li>
  <li style="width:132px">ULTRALIGHT</li>
  <li style="width:108px">INSPIRE</li>
  <li style="width:107px">REVIEWS</li>
  <li style="width:110px">ON SALE</li>
  </ul>
</nav>

<main>
  <div class="abs frame"></div>
  <div class="abs hero" role="img" aria-label="Woman in a pink jacket running along a grassy coastal trail above the sea"></div>

  <aside class="abs sidebar">
    <div class="abs current"></div>
    <ul>
      <li class="on" style="top:8px">Jackets</li>
      <li style="top:36px">Pants</li>
      <li style="top:63px">Tops</li>
      <li style="top:88px">Long Underwear &amp; Baselayers</li>
      <li style="top:114px">Dresses &amp; Skirts</li>
      <li style="top:139px">Shorts</li>
      <li style="top:165px">Sunglasses</li>
      <li style="top:191px">Watches</li>
      <li style="top:216px">Underwear</li>
      <li style="top:242px">Swimwear</li>
      <li style="top:268px">Women's Accessories</li>
      <li style="top:293px">Shoes &amp; Footwear</li>
    </ul>
  </aside>

  <section class="abs content"></section>
  <div class="abs cat-thumb"><div role="img" aria-label="Red women's jacket"></div></div>
  <h1 class="abs cat-title">WOMENS JACKETS &amp; COATS</h1>
  <div class="abs links" style="left:544px;top:320px">Snowboard Jackets<br>Down Jackets<br>Rain &amp; Wind Jackets<br>Casual Jackets<br>Fleece Jackets</div>
  <div class="abs links" style="left:694px;top:320px">Ski Jackets<br>Softshell Jackets<br>Bike Jackets<br>Synthetic Insulated Jackets<br>Vests</div>
  <div class="abs links" style="left:861px;top:320px">Performance Jackets<br>Technical Shells<br>Snowsuits</div>
  <p class="abs intro">Lorem ipsum dolor sit amet, consectetuer adipiscing elit, sed diam nonummy nibh euismod tincidunt ut laoreet dolore magna aliquam erat volutpat. Ut wisi enim ad minim veniam, quis nostrud exerci tation ullamcorper suscipit lobortis nisl ut aliquip..</p>

  <div class="abs subcats">
    <div class="subcat" style="left:27px"><h3>Snowboard<br>Jackets</h3><div class="img"><div role="img" aria-label="Lime and teal snowboard jacket" style="background:linear-gradient(180deg,#d8ec2a 0,#c9e01e 55%,#1f5a5c 56%,#1f5a5c 100%)"></div></div></div>
    <div class="subcat" style="left:131px"><h3>Down<br>Jackets</h3><div class="img"><div role="img" aria-label="Long dark purple down coat" style="background:linear-gradient(180deg,#3a3650,#25233a)"></div></div></div>
    <div class="subcat" style="left:236px"><h3>Rain &amp; Wind<br>Jackets</h3><div class="img"><div role="img" aria-label="Black rain jacket" style="background:linear-gradient(180deg,#e8e4e0 0,#2a2a2a 30%,#1a1a1a 100%)"></div></div></div>
  </div>

  <h2 class="abs featured-title">FEATURED PRODUCTS</h2>
  <svg class="abs next" viewBox="0 0 16 16"><rect width="16" height="16" fill="#777"/><path d="M6 4l4 4-4 4" fill="none" stroke="#fff" stroke-width="2"/></svg>
  <div class="product" style="left:800px"><div class="img"><div role="img" aria-label="Black boot bag" style="background:#1e2430"></div></div><p>Boot Bag 30L</p></div>
  <div class="product" style="left:890px"><div class="img"><div role="img" aria-label="Black travel backpack" style="background:#2a2a2a"></div></div><p>Transit Pack</p></div>
</main>

<footer>
  <div class="abs footer"></div>
  <div class="abs brands"><div class="inner">
    <span><i></i>Ridgeway</span><span>Talusline</span><span>Frostwing</span><span>Verdana Trail</span><span>Miravel</span><span>Southcape</span>
  </div></div>
  <div class="abs footlinks"><a href="#">Site Services</a><a href="#">Privacy and Security</a><a href="http://qlt.example/t-returns.aspx">Return Policy</a><a href="#">Shipping Rates</a><a href="#">Terms &amp; Conditions</a></div>
  <p class="abs copyright">Copyright © 2012 Quillton Peak Outfitters Inc. All Rights Reserved</p>

  <h4 class="abs foot-h" style="left:708px;top:685px">QUILLTON PEAK STORES</h4>
  <ul class="abs stores" style="left:708px;top:708px"><li>Alderbrook</li><li>Cedarfall</li><li>Copperton</li><li>Marten Ridge</li><li>Fernvale</li><li>Holloway</li></ul>
  <ul class="abs stores" style="left:788px;top:708px"><li>Granite Bay</li><li>Elk Hollow</li><li>Larchmont</li><li>Brackwell</li><li>Stonebury</li><li>Westhaven</li><li>Kestrel/Millbank</li></ul>

  <h4 class="abs foot-h" style="left:885px;top:685px">FIND US AT</h4>
  <div class="abs social"><span role="img" aria-label="Social channel one"></span><span role="img" aria-label="Social channel two"></span><span role="img" aria-label="Social channel three"></span></div>

  <h4 class="abs foot-h" style="left:885px;top:755px">CONTACT</h4>
  <div class="abs contact-row" style="left:886px;top:779px"><svg width="8" height="13" viewBox="0 0 8 13"><rect x=".5" y=".5" width="7" height="12" rx="1.5" fill="none" stroke="#fff"/><rect x="2" y="2" width="4" height="7" fill="#fff"/></svg>+1 (555) 014 2290</div>
  <div class="abs contact-row" style="left:885px;top:799px"><svg width="11" height="8" viewBox="0 0 11 8"><rect width="11" height="8" fill="#fff"/><path d="M0 0l5.5 4.5L11 0" fill="none" stroke="#2a7ac3"/></svg>hello@QuilltonPeak.example</div>
</footer>

</body>
</html>
```